Recruitment Site Design

We need a design for the login page, about page, and inner pages of a recruitment site for an oil and gas company. Design should be modern, sleek, professional and colors can be blue, green, white, orange or any other recommended colors.

Please also take into consideration that once the users login, they will need to access a form to fill in their information.

** UPDATE: Kindly provide a design for the inner information page consistent with the outer design. Attached is a picture of the basic structure. ***
Updates

Please provide a design for inner pages as shown in the design brief consistent with the registration page provided. 

Reason: We're extending it to get more inside pages.

Target Market(s)

Professionals looking for a career in the oil and gas industry in the Middle East.

Industry/Entity Type

Oil And Gas

Requirements
Must have
• Sleek design

```html
<!DOCTYPE html>
<html lang="en">
<head>
<meta charset="utf-8">
<title>Petrova — Oil &amp; Gas Careers</title>
<link href="https://fonts.googleapis.com/css2?family=PT+Sans:ital,wght@0,400;0,700;1,400;1,700&family=PT+Sans+Narrow:wght@700&display=swap" rel="stylesheet">
<style>
:root{
  --orange:#f5a300;
  --orange-dark:#ee8a00;
  --accent:#f07d14;
  --ink:#333;
  --text:#555;
  --muted:#777;
  --line:#dedede;
  --panel:#fafafa;
  --ground:#efefef;
  --dark:#3c3c3c;
  --sea:#4a6f9f;
}
*{box-sizing:border-box;margin:0;padding:0}
html,body{width:960px;height:1200px;overflow:hidden}
body{font-family:"PT Sans",sans-serif;color:var(--text);background:var(--ground);position:relative}
.top-band{position:absolute;left:0;top:0;width:960px;height:326px;background:linear-gradient(#f7b500,#f29c00)}
.page{position:absolute;left:96px;top:0;width:768px;height:1132px;background:#fff;box-shadow:0 0 6px rgba(0,0,0,.15)}
.abs{position:absolute}
.brand{left:18px;top:26px;font-size:40px;font-weight:700;color:#4a4a4a;letter-spacing:1px;line-height:1}
.utility{right:9px;top:17px;font-size:10.5px;color:#666}
.utility span{margin:0 5px;color:#aaa}
.nav{left:8px;top:90px;width:752px;height:44px;background:linear-gradient(#fbfbfb,#ececec);border:1px solid #d6d6d6;border-bottom:3px solid #c9c9c9;border-radius:3px;display:flex;align-items:center}
.nav a{font-size:10.5px;font-weight:700;color:#333;text-decoration:none;height:100%;display:flex;align-items:center;padding:0 19px;border-right:1px solid #ddd}
.nav a.active{background:linear-gradient(#f8ad10,#f39400);color:#fff;padding:0 22px;border:none}
.nav a:nth-child(7){border-right:none}
.nav-search{position:absolute;right:12px;top:10px;width:164px;height:21px;background:#fff;border:1px solid #ccc;border-radius:2px;font-size:9px;font-style:italic;color:#999;padding:4px 9px}
.nav-search .go{position:absolute;right:-1px;top:-1px;width:31px;height:21px;background:var(--orange);border-radius:0 2px 2px 0}
.slider{left:7px;top:146px;width:754px;height:328px;border:1px solid #ddd;padding:3px}
.slide{width:746px;height:320px;background:linear-gradient(#7f98bd 0%,#9fb2cc 30%,#7d8ea3 50%,#2f5a92 55%,#284f85 100%)}
.caption{left:404px;top:84px;width:346px;height:136px;background:rgba(50,50,50,.88);padding:10px 16px;color:#eee}
.caption h2{font-family:"PT Sans Narrow",sans-serif;font-size:21px;color:#fff;line-height:1.1}
.caption h3{font-size:14px;color:var(--accent);font-weight:700;line-height:1.3}
.caption p{font-size:10.5px;line-height:17px;margin-top:3px}
.job-search{position:relative;margin-top:7px;width:274px;height:24px;background:#fff;border:1px solid #bbb;font-size:10.5px;font-style:italic;color:#999;padding:4px 10px}
.job-search b{position:absolute;right:1px;top:1px;height:20px;padding:0 8px;background:var(--accent);color:#fff;font-style:normal;font-size:10.5px;line-height:20px}
.dots{left:12px;top:290px;width:87px;height:21px;background:rgba(40,40,40,.75);border-radius:11px;display:flex;gap:4px;align-items:center;padding-left:11px}
.dots i{width:10px;height:10px;border-radius:50%;background:#bbb}
.dots i:first-child{background:#fff}
.services{left:0;top:500px;width:768px;text-align:center}
.services h2{font-size:18px;font-weight:400;color:#444}
.services p{font-size:12px;font-style:italic;color:#888;line-height:22.4px;margin:10px 75px 0}
.rule{left:8px;top:624px;width:752px;height:1px;background:var(--line)}
.section-title{font-size:18px;font-weight:400;color:#444}
.section-title small{font-size:11px;font-style:italic;color:#666;margin-left:10px}
.job{left:8px;width:496px;height:104px}
.job.shade{background:var(--panel);border:1px solid #eaeaea}
.thumb{position:absolute;left:8px;top:14px;width:86px;height:77px;border:3px solid #fff;outline:1px solid #ddd}
.job h4{position:absolute;left:106px;top:12px;font-size:11px;font-weight:700;color:#444}
.job h4 em{font-style:normal;color:var(--accent)}
.job h4 span{margin:0 6px;color:#666}
.job p{position:absolute;left:106px;top:30px;width:370px;font-size:8.8px;line-height:14.4px;color:#777}
.job .meta{position:absolute;left:106px;top:80px;font-size:9.5px;font-style:italic;color:#777;display:flex;align-items:center}
.meta b{font-weight:400;color:#444}
.btn{display:inline-block;width:61px;height:18px;border-radius:2px;font-size:10.5px;font-weight:700;font-style:normal;text-align:center;line-height:18px;color:#fff}
.btn.dark{background:#333;margin-left:10px}
.btn.amber{background:var(--orange);margin-left:9px}
.sponsor{left:520px;top:674px;width:240px;height:95px;border:1px solid #ddd;display:flex;align-items:center;justify-content:center;gap:8px}
.sponsor .dot{width:22px;height:22px;border-radius:50%;background:#3da3e0}
.sponsor b{font-size:22px;font-weight:400;color:#2a7fc2}
.testimonials{left:520px;top:782px;width:240px;height:330px;border:1px solid #ddd;background:var(--panel);border-radius:3px;overflow:hidden}
.testimonials h2{height:34px;background:#6d6d6d;color:#fff;font-size:18px;font-weight:400;padding:4px 12px}
.quote{position:relative;height:145px;margin:0 11px;border-bottom:1px solid #e2e2e2}
.quote p{padding-top:12px;font-size:10.2px;font-style:italic;line-height:16px;color:#666}
.quote p q{quotes:none;color:var(--accent);font-size:22px;font-weight:700;font-style:normal;line-height:0;vertical-align:-6px;margin-right:5px}
.quote p strong{color:#222}
.quote .who{position:absolute;right:71px;top:118px;text-align:right;font-size:9px;color:#777;line-height:12px}
.quote .who b{display:block;font-size:10px;font-style:italic;color:#444}
.quote .face{position:absolute;right:1px;top:82px;width:70px;height:60px;border:2px solid #fff;outline:1px solid #ddd;background:linear-gradient(#b9c6d4,#d9c2ae)}
.quote:last-child{border:none}
.footer{left:105px;top:1160px;font-size:9.5px;color:#666}
.footer em{font-style:normal;color:var(--accent)}
.social{left:785px;top:1162px;display:flex;gap:6px}
.social i{width:13px;height:13px;border-radius:2px;background:#3b6ea8}
.social i:last-child{background:#f07d14}
</style>
</head>
<body>
<div class="top-band"></div>
<div class="page">
  <div class="abs brand">Petrova</div>
  <div class="abs utility">Support<span>|</span>FAQ<span>|</span>Login<span>|</span>Register</div>

  <nav class="abs nav">
    <a class="active">HOME</a><a>ABOUT US</a><a>JOBS</a><a>BLOG</a><a>FIND NOW</a><a>LOCATION</a><a>CONTACT</a>
    <div class="nav-search">Search here..<span class="go">
      <svg width="31" height="21" viewBox="0 0 31 21"><circle cx="14" cy="9" r="4.5" fill="none" stroke="#222" stroke-width="2"/><line x1="17" y1="12" x2="21" y2="16" stroke="#222" stroke-width="2.5"/></svg></span></div>
  </nav>

  <section class="abs slider">
    <div class="slide" role="img" aria-label="Offshore oil drilling platform in a bay with hills and city behind"></div>
    <div class="abs caption">
      <h2>Job in Oil &amp; Gas Industry</h2>
      <h3>Apply Now For Middle East Jobs</h3>
      <p>Sed accumsan sollicitudin sapien, sit amet adipiscing turpis gravida ac. In congue, neque ac lobortis volutpat..</p>
      <div class="job-search">Search for your perfect job....<b>SEARCH</b></div>
    </div>
    <div class="abs dots"><i></i><i></i><i></i><i></i><i></i></div>
  </section>

  <section class="abs services">
    <h2>Little About Our Services</h2>
    <p>Vestibulum ante ipsum primis in faucibus orci luctus et ultrices posuere cubilia Curae; Ut et scelerisque ante. Donec erat purus, faucibus vitae congue vel, porttitor nec lectus. Aenean a nibh eget turpis vehicula tempus ac sed massa.</p>
  </section>
  <div class="abs rule"></div>

  <h2 class="abs section-title" style="left:9px;top:638px">Recent Jobs Opening<small>(View All)</small></h2>
  <h2 class="abs section-title" style="left:520px;top:638px">Our Sponsors</h2>

  <article class="abs job shade" style="top:674px">
    <div class="thumb" role="img" aria-label="Worker in orange hard hat" style="background:linear-gradient(#6f9ed0,#c2572a)"></div>
    <h4><em>Name of Job</em><span>|</span>Oil &amp; Gas Industry Company</h4>
    <p>Aliquam molestie, mi et imperdiet euismod, dui purus auctor tellus, et interdum lacus lectus et ante. Sed accumsan sollicitudin sapien, sit amet adipiscing turpis gravida ac. In congue, neque ac lobortis volutpat..</p>
    <div class="meta">Location:&nbsp;<b>Middle of East here</b><span class="btn dark">Details</span><span class="btn amber">Apply</span></div>
  </article>
  <article class="abs job" style="top:788px">
    <div class="thumb" role="img" aria-label="Engineer in white hard hat" style="background:linear-gradient(90deg,#d8d8d8,#2d3f74)"></div>
    <h4><em>Name of Job</em><span>|</span>Oil &amp; Gas Industry Company</h4>
    <p>Aliquam molestie, mi et imperdiet euismod, dui purus auctor tellus, et interdum lacus lectus et ante. Sed accumsan sollicitudin sapien, sit amet adipiscing turpis gravida ac. In congue, neque ac lobortis volutpat..</p>
    <div class="meta">Location:&nbsp;<b>Middle of East here</b><span class="btn dark">Details</span><span class="btn amber">Apply</span></div>
  </article>
  <article class="abs job shade" style="top:910px">
    <div class="thumb" role="img" aria-label="Engineers reviewing plans at a refinery" style="background:linear-gradient(#8aa2bd,#9bb54a)"></div>
    <h4><em>Name of Job</em><span>|</span>Oil &amp; Gas Industry Company</h4>
    <p>Aliquam molestie, mi et imperdiet euismod, dui purus auctor tellus, et interdum lacus lectus et ante. Sed accumsan sollicitudin sapien, sit amet adipiscing turpis gravida ac. In congue, neque ac lobortis volutpat..</p>
    <div class="meta">Location:&nbsp;<b>Middle of East here</b><span class="btn dark">Details</span><span class="btn amber">Apply</span></div>
  </article>
  <article class="abs job" style="top:1021px">
    <div class="thumb" role="img" aria-label="Workers silhouetted against a sunset" style="background:linear-gradient(#f2a21a,#2a1a08)"></div>
    <h4><em>Name of Job</em><span>|</span>Oil &amp; Gas Industry Company</h4>
    <p>Aliquam molestie, mi et imperdiet euismod, dui purus auctor tellus, et interdum lacus lectus et ante. Sed accumsan sollicitudin sapien, sit amet adipiscing turpis gravida ac. In congue, neque ac lobortis volutpat..</p>
    <div class="meta">Location:&nbsp;<b>Middle of East here</b><span class="btn dark">Details</span><span class="btn amber">Apply</span></div>
  </article>

  <div class="abs sponsor"><span class="dot"></span><b>Meridian</b></div>

  <aside class="abs testimonials">
    <h2>Testimonials</h2>
    <div class="quote">
      <p><q>“</q>In congue, neque ac lobortis volutpat, libero mauris varius mi, vitae suscipit ipsum ligula vitae risus. Duis aliquam nibh a dui iaculis viverra id a velit....<strong>Read More</strong></p>
      <div class="who"><b>Daniel Reyes</b>Senior assistant</div>
      <div class="face" role="img" aria-label="Portrait of Daniel Reyes"></div>
    </div>
    <div class="quote">
      <p><q>“</q>In congue, neque ac lobortis volutpat, libero mauris varius mi, vitae suscipit ipsum ligula vitae risus. Duis aliquam nibh a dui iaculis viverra id a velit....<strong>Read More</strong></p>
      <div class="who"><b>Laura Stein</b>Selection Officer</div>
      <div class="face" role="img" aria-label="Portrait of Laura Stein"></div>
    </div>
  </aside>
</div>

<footer class="abs footer">Copyright © 2012 &nbsp;<em>Petrova.</em> All Right Reserved &nbsp;|&nbsp; Privacy Policy</footer>
<div class="abs social"><i></i><i></i><i></i><i></i></div>
</body>
</html>
```